Veranix - Solution provider in business consulting

Veranix is a swiss based company providing solutions for developing markets. The business covers various fields of business consulting, such as supply chain, product costs, quality management and manufacturing management. The Business operates in a efficient, straight and solution oriented manner.
The final design should communicate these characteristics. Asian people as well as as western people shall identify the qualities of the company at first sight.
The customer needs business cards with a simple view but an recognizable design, printed in high quality. Engraved elements such as the globe or simple words are possible.
Available colors are: (RAL)
102/102/102
51/102/102
153/204/153
255/102/51
Font: Calibri

```html
<!DOCTYPE html>
<html lang="en">
<head>
<meta charset="utf-8">
<title>Veranix business cards</title>
<link href="https://fonts.googleapis.com/css2?family=Carlito:wght@400;700&display=swap" rel="stylesheet">
<style>
  :root {
    --backdrop: #3b3430;
    --card: #0c0c0c;
    --card-edge: #1c1c1c;
    --silver: #c9c9c9;
    --silver-soft: #a9a9a9;
    --name-grey: #666666;
    --rule: #2a2a2a;
    --mark-grey: #8a8a8a;
  }
  * { margin: 0; padding: 0; box-sizing: border-box; }
  html, body {
    width: 1200px; height: 900px; overflow: hidden;
    background: var(--backdrop);
    font-family: "Carlito", "Calibri", sans-serif;
  }
  .sheet {
    position: relative; width: 1200px; height: 900px;
    display: flex; align-items: center; justify-content: center; gap: 48px;
  }
  .card {
    position: relative; width: 540px; height: 310px;
    background: var(--card);
    border: 1px solid var(--card-edge);
    box-shadow: 0 14px 30px rgba(0,0,0,.45);
    overflow: hidden;
  }
  /* contact side */
  .card-contact .mark-area {
    position: absolute; left: 44px; top: 70px; width: 170px; height: 170px;
  }
  .card-contact .divider {
    position: absolute; left: 262px; top: 58px; bottom: 58px;
    width: 1px; background: var(--rule);
  }
  .details {
    position: absolute; left: 284px; top: 52px;
    color: var(--silver); font-size: 15px; line-height: 1.18;
  }
  .details .person-name { color: var(--name-grey); font-weight: 700; font-size: 17px; }
  .details .person-role { margin-bottom: 14px; }
  .details .address { margin-bottom: 12px; }
  .contact-list { list-style: none; }
  .contact-list li { display: flex; align-items: center; gap: 10px; height: 19px; }
  .contact-list svg { width: 11px; height: 11px; flex: none; }
  /* logo side */
  .card-logo { display: flex; align-items: center; justify-content: center; }
  .wordmark {
    display: flex; align-items: center; gap: 16px;
    color: var(--silver); font-size: 62px; font-weight: 400; letter-spacing: 1px;
  }
  .wordmark .dot {
    width: 34px; height: 34px; border-radius: 50%; background: var(--silver);
  }
</style>
</head>
<body>
<main class="sheet">
  <section class="card card-contact">
    <svg class="mark-area" viewBox="0 0 170 170" role="img" aria-label="Decorative area for the company emblem, plain grey disc">
      <circle cx="85" cy="85" r="82" fill="var(--mark-grey)"/>
    </svg>
    <div class="divider"></div>
    <div class="details">
      <p class="person-name">Martin Aebi</p>
      <p class="person-role">CEO</p>
      <p class="address">Veranix GmbH Lindenweg 14<br>8410 Winterthal Switzerland</p>
      <ul class="contact-list">
        <li><svg viewBox="0 0 12 12"><rect x="3" y="0.5" width="6" height="11" rx="1" fill="none" stroke="var(--silver-soft)" stroke-width="1.2"/></svg>+41 79 382 5107</li>
        <li><svg viewBox="0 0 12 12"><path d="M2 1 L4.5 1 L5 4 L3.6 5 Q5 8 7 8.4 L8 7 L11 7.5 L11 10 Q6 11.5 1 4 Z" fill="var(--silver-soft)"/></svg>+41 71 640 2918</li>
        <li><svg viewBox="0 0 12 12"><rect x="0.5" y="2" width="11" height="8" fill="none" stroke="var(--silver-soft)" stroke-width="1.2"/><path d="M0.5 2 L6 6.5 L11.5 2" fill="none" stroke="var(--silver-soft)" stroke-width="1.2"/></svg>martin.aebi@veranix.ch</li>
        <li><svg viewBox="0 0 12 12"><circle cx="6" cy="6" r="5.5" fill="var(--silver-soft)"/></svg>www.veranix.ch</li>
      </ul>
    </div>
  </section>

  <section class="card card-logo">
    <div class="wordmark"><span>Veranix</span><span class="dot"></span></div>
  </section>
</main>
</body>
</html>
```